Boutique custom software development company needs new business card

Our nearly 20 year old custom software development company would like to better include the fact that we are now providing Bitcoin services. These new services are B2B include education (how to acquire and securely hold Bitcoin) and integrating Bitcoin payments into existing ecommerce sites or other existing systems. Please keep the card clean and simple. Attached is our current design and some other files. vextorial.com

Target Market(s)

businesses owners interested in long term relationship

Industry/Entity Type

Custom software development and Bitcoin

Contact Information for Business Card

Dale Parker, dale@vextorial.com, vextorial.com, (888) 555-VXTRL

Font styles to use
Other font styles liked:
• monospace

Requirements
Must have
• double-sided
Nice to have
• clean and simple
Should not have
• physical address

```html
<!DOCTYPE html>
<html lang="en">
<head>
<meta charset="utf-8">
<title>Vextorial Business Card</title>
<link rel="stylesheet" href="https://fonts.googleapis.com/css2?family=Montserrat:wght@600;800&family=Open+Sans:wght@400;600&display=swap">
<style>
  :root {
    --backdrop: #e4e4e2;
    --card: #303030;
    --card-deep: #1c1c1c;
    --edge: #e0701c;
    --orange: #f07a1e;
    --blue: #3f76c0;
    --white: #ffffff;
    --grey-text: #e8e8e8;
    --panel-light: #6a6a6a;
  }
  * { margin: 0; padding: 0; box-sizing: border-box; }
  html, body {
    width: 1200px; height: 801px; overflow: hidden;
    background: var(--backdrop);
  }
  .canvas {
    position: relative; width: 1200px; height: 801px;
    display: flex; align-items: center; justify-content: center; gap: 44px;
  }
  .card {
    position: relative; width: 540px; height: 309px;
    background: var(--card);
    border-bottom: 4px solid var(--edge);
    border-left: 2px solid var(--edge);
    box-shadow: 0 14px 30px rgba(0,0,0,0.22);
    overflow: hidden;
    font-family: "Open Sans", sans-serif;
  }

  /* Front */
  .brand-block { position: absolute; left: 120px; top: 58px; }
  .brand-name {
    font-family: "Montserrat", sans-serif; font-weight: 800;
    font-size: 48px; letter-spacing: 1px; line-height: 1;
    color: var(--blue);
  }
  .tagline {
    font-size: 16px; color: var(--blue); margin-top: 6px; letter-spacing: 0.2px; line-height: 1.35;
  }
  .details { position: absolute; left: 56px; top: 196px; display: flex; align-items: stretch; }
  .person { padding-right: 20px; }
  .person-name {
    font-family: "Montserrat", sans-serif; font-weight: 800; font-size: 19px;
    letter-spacing: 0.5px; line-height: 1.2;
  }
  .first { color: var(--orange); }
  .last { color: var(--blue); }
  .services { font-size: 12.5px; color: var(--grey-text); line-height: 1.5; margin-top: 4px; }
  .divider { width: 1px; background: #bdbdbd; margin: 0 4px; }
  .contacts { list-style: none; padding-left: 20px; }
  .contacts li {
    display: flex; align-items: center; gap: 9px;
    font-size: 13px; color: var(--grey-text); line-height: 1.7;
  }
  .contacts svg { width: 13px; height: 13px; flex: none; }

  /* Back */
  .back-panel {
    position: absolute; left: 0; top: 0; bottom: 0; width: 205px;
    background: linear-gradient(160deg, var(--card-deep) 0%, #2c2c2c 45%, var(--panel-light) 100%);
  }
  .back-brand { position: absolute; left: 234px; top: 112px; }
  .back-brand .brand-name { color: var(--white); font-size: 42px; }
  .back-brand .tagline { color: var(--white); font-size: 15px; }
</style>
</head>
<body>
<main class="canvas">

  <section class="card card-front" aria-label="Card front">
    <div class="brand-block">
      <div class="brand-name">VEXTORIAL</div>
      <div class="tagline">developer of custom applications</div>
    </div>
    <div class="details">
      <div class="person">
        <div class="person-name"><span class="first">DALE</span> <span class="last">PARKER</span></div>
        <div class="services">Bitcoin education &amp;<br>payment integration</div>
      </div>
      <div class="divider"></div>
      <ul class="contacts">
        <li>
          <svg viewBox="0 0 16 16"><path d="M4 1.5l2.5 3-1.5 1.6c.8 1.9 2.1 3.2 4 4l1.6-1.5 3 2.5-1.7 2.4C7.3 13.3 2.7 8.7 1.6 3.2z" fill="var(--orange)"/></svg>
          (888) 555-VXTRL
        </li>
        <li>
          <svg viewBox="0 0 16 16"><rect x="1.5" y="3.5" width="13" height="9" fill="none" stroke="var(--orange)" stroke-width="1.5"/><path d="M1.5 3.5l6.5 5 6.5-5" fill="none" stroke="var(--orange)" stroke-width="1.5"/></svg>
          dale@vextorial.com
        </li>
        <li>
          <svg viewBox="0 0 16 16"><circle cx="8" cy="8" r="6.5" fill="none" stroke="var(--orange)" stroke-width="1.4"/><ellipse cx="8" cy="8" rx="3" ry="6.5" fill="none" stroke="var(--orange)" stroke-width="1.2"/><path d="M1.5 8h13M2.5 4.8h11M2.5 11.2h11" stroke="var(--orange)" stroke-width="1.1"/></svg>
          www.vextorial.com
        </li>
      </ul>
    </div>
  </section>

  <section class="card card-back" aria-label="Card back">
    <div class="back-panel" role="img" aria-label="Embossed brand decoration area"></div>
    <div class="back-brand">
      <div class="brand-name">VEXTORIAL</div>
      <div class="tagline">developer of custom applications<br>&amp; bitcoin services</div>
    </div>
  </section>

</main>
</body>
</html>
```